Clear Plastic Card Design

I am looking to have a business card designed from my logo icon. I am looking to match the style of a different business card I have attached in the files.
Looking for a card that is plastic, with layers of transparency in the shape of my logo icon (also attached in the files) - not a circle like the other card. The winning design will incorporate the red icon logo on the front and back and include the charity's name, "Light for the Weary Souls" in the same or similar font, as well as an email and phone number. For now, use the email: email@lightfortheweary-mail.org and the phone number 555-382-7194.
We like how the sample business card has transparency, partial and full opacity layers and a matching color scheme. Files will need to be in vector so that our business card printing company can work with it.
UPDATE:
We've some excellent designs in, thank you everyone! I got an early review from the owner, and he requested a minor redirect to find his perfect design. He wants the design to stand out by NOT being a rectangle. Try instead a circle, square, or best yet - something that falls in the outline of the logo icon, either fully or partially. Thank you, everyone!
Light for the Weary Souls text should be incorporated as well as a phone and email.

```html
<!DOCTYPE html>
<html lang="en">
<head>
<meta charset="utf-8">
<title>Light for the Weary Souls – Round Card</title>
<link href="https://fonts.googleapis.com/css2?family=Roboto+Condensed:wght@700&display=swap" rel="stylesheet">
<style>
  :root {
    --page: #ecebe8;
    --card: #d3d3d2;
    --card-edge: #4a4a48;
    --band: #64646a;
    --band-text: #ffffff;
    --halo: #f7f7f7;
    --core: #b9b9b8;
    --core-edge: #3d3d3b;
    --ink: #3d3d3b;
  }
  html, body {
    margin: 0;
    width: 1200px;
    height: 1200px;
    overflow: hidden;
    background: var(--page);
  }
  .card {
    display: block;
    width: 1200px;
    height: 1200px;
  }
  .card-text {
    font-family: "Roboto Condensed", "Arial Narrow", sans-serif;
    font-weight: 700;
  }
  .ring-text {
    fill: var(--band-text);
    font-size: 44px;
    letter-spacing: 1px;
  }
  .ring-dot { fill: var(--band-text); }
  .name-mark {
    fill: var(--ink);
    font-size: 54px;
  }
  .sketch-line {
    fill: none;
    stroke: var(--card-edge);
    stroke-width: 3;
  }
</style>
</head>
<body>
<svg class="card" viewBox="0 0 1200 1200" xmlns="http://www.w3.org/2000/svg">
  <defs>
    <radialGradient id="card-sheen" cx="45%" cy="40%" r="65%">
      <stop offset="0" stop-color="#e6e6e5"/>
      <stop offset="1" stop-color="var(--card)"/>
    </radialGradient>
    <path id="upper-arc" d="M600,980 A380,380 0 1 1 600,220 A380,380 0 1 1 600,980"/>
    <path id="lower-arc" d="M185,600 A415,415 0 0 0 1015,600"/>
  </defs>

  <!-- clear outer disc -->
  <circle cx="600" cy="600" r="520" fill="url(#card-sheen)" stroke="var(--card-edge)" stroke-width="6"/>

  <!-- loose overlapping outlines -->
  <ellipse class="sketch-line" cx="625" cy="585" rx="495" ry="480" transform="rotate(-12 625 585)"/>
  <ellipse class="sketch-line" cx="590" cy="615" rx="500" ry="470" transform="rotate(20 590 615)"/>
  <ellipse class="sketch-line" cx="640" cy="610" rx="470" ry="490"/>

  <!-- contact band -->
  <circle cx="600" cy="600" r="430" fill="var(--band)"/>
  <circle cx="600" cy="600" r="365" fill="var(--halo)"/>

  <!-- inner core -->
  <circle cx="600" cy="600" r="305" fill="#dcdcdb"/>
  <circle cx="600" cy="600" r="270" fill="var(--core)" stroke="var(--core-edge)" stroke-width="12"/>

  <!-- ring lettering -->
  <text class="card-text ring-text" text-anchor="middle">
    <textPath href="#upper-arc" startOffset="25%">555-382-7194</textPath>
  </text>
  <text class="card-text ring-text" text-anchor="middle">
    <textPath href="#upper-arc" startOffset="62%">EMAIL@LIGHTFORTHEWEARY-MAIL.ORG</textPath>
  </text>
  <text class="card-text ring-text" text-anchor="middle">
    <textPath href="#lower-arc" startOffset="50%">LIGHT FOR THE WEARY SOULS</textPath>
  </text>

  <!-- separators -->
  <circle class="ring-dot" cx="318" cy="882" r="8"/>
  <circle class="ring-dot" cx="318" cy="318" r="8"/>
  <circle class="ring-dot" cx="882" cy="882" r="8"/>

  <!-- name in the centre -->
  <text class="card-text name-mark" x="600" y="580" text-anchor="middle">Light for the</text>
  <text class="card-text name-mark" x="600" y="648" text-anchor="middle">Weary Souls</text>
</svg>
</body>
</html>
```